Push notification screens at app start up

We have an existing news publication app platform and are adding categories to push notifications.

We need two screens designed (each for Zorbel, Quillet and Android for a total of 6d) that show when the app is first launched.

The workflow of our app:
0. app launch screen while webservices run (no work needed)
1. information screen to the user promoting the benefits of push notification with "Next" button. (see concept attached)
2. Push categories selection screen. This will have list of category types, with on/off switch.

"Select the categories that you wish to receive occasional notices:
Breaking News (on/off switch)
Local News (on/off switch)
Sports (on/off switch)
Local Events (on/off switch)
Weather Alerts (on/off switch)
Local Deals (on/off switch)"

"Enable these categories on the next screen."
"Next" button

Background:
When I was looking around at app designs, I came across this one (http://www.plinthworks.example/design/7719034) and I really liked it. We obviously have different features on our screen, but I’d like to have this same feel. The colors used in this design are perfect.

UPDATE: I do not mean to limit your design to match the layout as the one mentioned above. Please use your creativity for the layout.

Our standard font in Helvetica Neue.

Notes:
- our app is developed for all phone devices from Zorbel 4 to Zorbel 6, so designs should be thoughtful of vertical scrolling if needed.
- our app is developed for Quillets, so we'll need designs completed as well. (We can finalize Zorbel design first, then translate the design to Quillet.)
- our app is developed for Android phones (not tablets), so we'll need designs completed as well. (We can finalize iOS design first, then translater to Android UI design guidelines).

We hope to establish a good on-going relationship with the designer for as-needed work in the future.

News

• Helvetica Neue

• Clean designs. No clutter.
• We would likely go with the standard on/off switches for both iOS and Android, but are open to small custom variations.

```html
<!DOCTYPE html>
<html lang="en">
<head>
<meta charset="utf-8">
<title>Notifications</title>
<link rel="stylesheet" href="https://fonts.googleapis.com/css2?family=Arimo:wght@400;700&display=swap">
<style>
  :root {
    --brand-blue: #2d6ff0;
    --switch-blue: #2a6fe8;
    --night: #000000;
    --paper: #ffffff;
    --label-grey: #6b6b6b;
    --icon-grey: #8a8a8a;
    --rule: #e2e2e2;
    --switch-track: #e6e6e6;
  }
  * { box-sizing: border-box; margin: 0; padding: 0; }
  html, body {
    width: 675px;
    height: 1200px;
    overflow: hidden;
    background: var(--night);
    font-family: "Arimo", "Helvetica Neue", Helvetica, Arial, sans-serif;
  }
  .screen {
    position: relative;
    width: 675px;
    height: 1200px;
    background: var(--night);
  }
  .app-header {
    height: 142px;
    background: var(--brand-blue);
    color: var(--paper);
    position: relative;
  }
  .status-bar {
    position: absolute;
    top: 12px;
    left: 0;
    right: 0;
    height: 30px;
    font-size: 23px;
    line-height: 30px;
  }
  .status-left {
    position: absolute;
    left: 12px;
    display: flex;
    align-items: center;
    gap: 8px;
  }
  .signal { display: flex; gap: 3px; }
  .signal span {
    width: 11px; height: 11px; border-radius: 50%;
    background: var(--paper);
  }
  .signal span.off { background: transparent; border: 1.5px solid var(--paper); }
  .status-time {
    position: absolute;
    left: 0; right: 0;
    text-align: center;
    font-weight: 700;
  }
  .status-right {
    position: absolute;
    right: 12px;
    display: flex;
    align-items: center;
    gap: 10px;
  }
  .battery {
    width: 52px; height: 22px;
    border: 2px solid var(--paper);
    border-radius: 4px;
    padding: 2px;
    position: relative;
  }
  .battery::before {
    content: ""; display: block; width: 100%; height: 100%;
    background: var(--paper); border-radius: 1px;
  }
  .battery::after {
    content: ""; position: absolute; right: -6px; top: 5px;
    width: 4px; height: 8px; background: var(--paper); border-radius: 0 2px 2px 0;
  }
  .nav-bar {
    position: absolute;
    top: 62px; left: 0; right: 0;
    height: 60px;
  }
  .back-button {
    position: absolute;
    left: 24px; top: 12px;
  }
  .nav-title {
    text-align: center;
    font-size: 36px;
    font-weight: 700;
    line-height: 60px;
  }
  .intro {
    height: 157px;
    color: var(--paper);
    font-size: 27px;
    line-height: 36px;
    text-align: center;
    padding-top: 44px;
  }
  .category-list {
    list-style: none;
    background: var(--paper);
  }
  .category {
    height: 99.5px;
    display: flex;
    align-items: center;
    border-bottom: 2px solid var(--rule);
    position: relative;
  }
  .category:last-child { border-bottom: none; }
  .category-icon { margin-left: 29px; width: 36px; height: 36px; }
  .category-name {
    margin-left: 36px;
    font-size: 29px;
    font-weight: 700;
    color: var(--label-grey);
  }
  .switch {
    position: absolute;
    right: 18px;
    width: 88px;
    height: 54px;
    border-radius: 27px;
    background: var(--paper);
    border: 3px solid var(--switch-track);
  }
  .switch::after {
    content: "";
    position: absolute;
    top: 0; left: 0;
    width: 48px; height: 48px;
    border-radius: 50%;
    background: var(--paper);
    box-shadow: 0 2px 5px rgba(0,0,0,0.3);
  }
  .switch.is-on { background: var(--switch-blue); border-color: var(--switch-blue); }
  .switch.is-on::after { left: auto; right: 0; }
</style>
</head>
<body>
<main class="screen">
  <header class="app-header">
    <div class="status-bar">
      <div class="status-left">
        <div class="signal"><span></span><span></span><span></span><span class="off"></span><span class="off"></span></div>
        <span class="carrier">KESTA</span>
        <svg width="24" height="18" viewBox="0 0 24 18" aria-hidden="true">
          <path d="M12 17 L2 6 A14 14 0 0 1 22 6 Z" fill="#fff"/>
        </svg>
      </div>
      <div class="status-time">4:21 PM</div>
      <div class="status-right">
        <svg width="12" height="20" viewBox="0 0 12 20" aria-hidden="true">
          <path d="M1 5 L10 14 L6 18 V2 L10 6 L1 15" fill="none" stroke="#fff" stroke-width="1.8"/>
        </svg>
        <span>100%</span>
        <div class="battery"></div>
      </div>
    </div>
    <nav class="nav-bar">
      <svg class="back-button" width="22" height="36" viewBox="0 0 22 36" aria-label="Back">
        <path d="M18 3 L4 18 L18 33" fill="none" stroke="#fff" stroke-width="5" stroke-linecap="square"/>
      </svg>
      <h1 class="nav-title">Notifications</h1>
    </nav>
  </header>

  <p class="intro">Select the categories of notices you<br>wish to receive:</p>

  <ul class="category-list">
    <li class="category">
      <svg class="category-icon" viewBox="0 0 36 36" aria-hidden="true"><rect x="3" y="5" width="30" height="26" fill="none" stroke="#8a8a8a" stroke-width="2.5"/><rect x="8" y="10" width="8" height="8" fill="#8a8a8a"/><path d="M19 11h9M19 16h9M8 22h20M8 26h20" stroke="#8a8a8a" stroke-width="2"/></svg>
      <span class="category-name">Breaking News</span>
      <span class="switch" role="switch" aria-checked="false"></span>
    </li>
    <li class="category">
      <svg class="category-icon" viewBox="0 0 36 36" aria-hidden="true"><rect x="3" y="5" width="30" height="26" fill="none" stroke="#8a8a8a" stroke-width="2.5"/><rect x="8" y="10" width="8" height="8" fill="#8a8a8a"/><path d="M19 11h9M19 16h9M8 22h20M8 26h20" stroke="#8a8a8a" stroke-width="2"/></svg>
      <span class="category-name">Local News</span>
      <span class="switch is-on" role="switch" aria-checked="true"></span>
    </li>
    <li class="category">
      <svg class="category-icon" viewBox="0 0 36 36" aria-hidden="true"><rect x="3" y="5" width="30" height="26" fill="none" stroke="#8a8a8a" stroke-width="2.5"/><rect x="8" y="10" width="8" height="8" fill="#8a8a8a"/><path d="M19 11h9M19 16h9M8 22h20M8 26h20" stroke="#8a8a8a" stroke-width="2"/></svg>
      <span class="category-name">Sports</span>
      <span class="switch" role="switch" aria-checked="false"></span>
    </li>
    <li class="category">
      <svg class="category-icon" viewBox="0 0 36 36" aria-hidden="true"><rect x="3" y="5" width="30" height="26" fill="none" stroke="#8a8a8a" stroke-width="2.5"/><rect x="8" y="10" width="8" height="8" fill="#8a8a8a"/><path d="M19 11h9M19 16h9M8 22h20M8 26h20" stroke="#8a8a8a" stroke-width="2"/></svg>
      <span class="category-name">Local Events</span>
      <span class="switch" role="switch" aria-checked="false"></span>
    </li>
    <li class="category">
      <svg class="category-icon" viewBox="0 0 36 36" aria-hidden="true"><rect x="3" y="5" width="30" height="26" fill="none" stroke="#8a8a8a" stroke-width="2.5"/><rect x="8" y="10" width="8" height="8" fill="#8a8a8a"/><path d="M19 11h9M19 16h9M8 22h20M8 26h20" stroke="#8a8a8a" stroke-width="2"/></svg>
      <span class="category-name">Weather Alerts</span>
      <span class="switch" role="switch" aria-checked="false"></span>
    </li>
    <li class="category">
      <svg class="category-icon" viewBox="0 0 36 36" aria-hidden="true"><rect x="3" y="5" width="30" height="26" fill="none" stroke="#8a8a8a" stroke-width="2.5"/><rect x="8" y="10" width="8" height="8" fill="#8a8a8a"/><path d="M19 11h9M19 16h9M8 22h20M8 26h20" stroke="#8a8a8a" stroke-width="2"/></svg>
      <span class="category-name">Local Deals</span>
      <span class="switch" role="switch" aria-checked="false"></span>
    </li>
  </ul>
</main>
</body>
</html>
```